Mobile Repair Service on location needs a Web Design

We are starting a new mobile device repair service called Handset Haven and our website needs a design!

Hello Designers!
First, we'd like to make clear this is more than a simple web design contest, we want the designers to create an idea. We want someone who can create the whole theme of the service's we provide. We want someone that can help design our visual branding, help us communicate a sentiment. And we are willing to pay for that.

Who are we?
Our company is based in Rotterdam, the Netherlands. We provide different services for all kinds of electronic devices. The kind of services we provide are, among other things, installations of hardware and software and the repair of broken or malfunctioning devices.
We are starting a new service that offers mobile device repairs on location, be it at the home of our customers, their office, or any other place. Just give us the address and we will come to you for the repair job. This is also our main USP. We have multiple skilled engineers who drive trough the country on a daily basis and can be on location within a working day. Repair is done immediately onsite while the customer waits. At this stage we will start with the smartphone product-group within the mobile devices. In a second phase we might also add tablets.
People don't want to be without their phone for weeks because of some parts that needed to be ordered by a repair center they had to sent their phone to. We offer a fully functional mobile repair center in the form of specially customized vans. These vans have all the tools and utilities needed by our engineers to safely repair your mobile device. Your phone is being repaired directly in front of you, the next business-day, on a location you desire.

For this new service we are creating a website called Handset Haven. The website needs a story and matching design and this is where you come in. We are not looking for a simple template design we can get from any place. We need a story. We want you to create an idea, build a unique theme or vision that helps sell the product/service. This goes beyond the design of the website. We need the whole package, the design you are creating needs to have returning elements like icons, color use, images, maybe even characters etc. You name it! There needs to be a common thread in the design so we can reuse elements in, for example, the email templates, the work order or receipt we give to our customers (we may contact the winner of the contest to design these for us as well!).

The name 'Handset Haven' is chosen. Rehab (short for rehabilitate) has a bold and playful tone to it and the design needs to reflect the name. So we're looking for a somewhat playful and cheeky design. Definitely not too serious and definitely modern. We already got a logo that we love and that fit's this description (see attached design documents for the logo). It's bold, powerful and fun. Our web design needs to reflect this as well and has to fit in with our logo.
We would really like it if the design somehow incorporates elements that highlight our unique selling points (repairs on location, we come to you etc.). We would really like some form of story telling in the design. Think clumsy people breaking their phones. Teenagers in tears because they have no access to their friends. People nowadays have the need to always be 'connected'. What happens when your phone is broken or malfunctioning? We're handling tech, we are nerds and a little bit weird, but we're professionals and here to help you with your problem. The sentiment Byte Brigade tries to communicate is something we really like. We're looking for fresh idea's, anything goes!

In an overview all Unique Selling Points of the Handset haven service:
- Professional service on location. Don’t ship to us we will come to you!
- Clear pricing upfront. No hidden cost.
- Next business-day repair.
- Backed by a professional call center open 12 hours a day and open on a Saturday as well
- Backed by a professional repair center with more then 12 years of experience
- Repair is done by certified engineers
- 1 year warranty on the repair

The process:
The main function of our website will be for customers to make a repair request. A customer will visit our website and can make a repair request immediately by going through a 'request-order-flow'. In this flow he or she will need to fill in some forms and can select wich type/model/brand of mobile device he or she has and what parts need to be repaired. After a request is placed we will call the customer back (within an hour) for a short intake and to set a date/time and location. Our engineer will meet the customer at the specified location and will repair the device onsite in one of our mobile repair centers, which is a specialized van equipped with all the tools needed for device restorations.
So in short the steps are:
- Choose your device and repair job
- Place the order
- Get a callback within the hour
- Set date and location
- We will come to you.

Website functionality:
Our website is our main form of communication. So the sentiment we want to communicate needs be reflected in the design. We need a main/front page designed (preferably a long scrolling page design) containing:
1. Customers will be able to request a repair job directly on our website. So there will need to be a prominent button/link at the top of our main page that will bring the customer to this 'request-order-flow'. This is the main flow which needs to be full focus on the front page. All other items are secondary.
2. The general information of who we are and what we do, and why the customer should choose us. Preferably in short bullet-point type keywords/sentences with icons or other visual cues. See our unique selling points to get an idea of the information that will be displayed here.
3. There needs to be a section that will explain the process (see above) of a repair request step-by- step, again in brief short key sentences and with (custom) icons.
4. There needs to be a section that explains to the customer he/she can always contact us if they are not sure what the problem is with their device, and for this reason are not sure what repair request they should order.
5. We want to implement some functionality that display customer ratings or customer reviews. So there needs to be room for some kind of widget of plugin we're going to implement which shows these reviews.
6. A 'For business section' where we will explain all the options we provide for corporate clients.
7. Social media links.
8. There needs to be a menu with buttons that leads to the all sections described in the previous points.

For now, we need a design for our front page. In the second phase, when we have picked our winner, we may ask the winner to design the page(s) for our request workflow as well.

EDIT:
Finally, we have a very specific order in mind for the different segments of our website. We would like you to add some more segments that were not in our original brief as well:

1. Top header with order/request button. (should instantly make clear our main USP, we do repairs on location)
2. Our process
3. Our unique selling points / why choose us
4. The kind of repairs we do (broken screens, broken batteries, water damage, broken camera's, no sound etc.)
5. A 'meet our team' section, where we introduce some of our engineers
6. A 'contact us for any questions' section/
7. Testimonials/user reviews
8. A section where we show key performance indicators
9. 'For businesses' sections
10.'Subscribe for newsletter' field
11. Social media buttons

Industry/Entity Type

It Service

Number of Pages Required

1 page

Font styles to use
Sans Serif

Requirements
Must have
• a main/front page, design only
• custom icons/images for banners, adverts online and in print (high res)
Nice to have
• Storytelling in our design.
• Design that fits with our brand new logo.
• Elements like icons to have a flat design.
• Keep in mind that the website will need to be responsive when designing! (Ideally provide an example of the mobile design as well)
• Create a fun and trustworthy feeling.

```html
<!DOCTYPE html>
<html lang="en">
<head>
<meta charset="utf-8">
<title>Handset Haven — Mobile Repair On Location</title>
<link href="https://fonts.googleapis.com/css2?family=Raleway:wght@300;400;500;600;700&display=swap" rel="stylesheet">
<style>
:root{
  --orange:#f26522;
  --orange-dark:#e0501a;
  --orange-light:#ff8a3d;
  --ink:#2b2b2b;
  --text:#555;
  --muted:#888;
  --line:#e3e3e3;
  --lavender:#e4e4f2;
  --ring:#c9c8ec;
  --footer:#1b1d20;
  --white:#fff;
}
*{margin:0;padding:0;box-sizing:border-box}
html,body{width:1200px;height:3797px;overflow:hidden}
body{font-family:'Raleway',Arial,sans-serif;color:var(--text);background:var(--white);position:relative}
section,header,footer{position:absolute;left:0;width:1200px}
a{color:inherit;text-decoration:none}
.btn{display:inline-block;background:var(--orange);color:var(--white);border-radius:20px;font-size:14px;font-weight:500;padding:10px 28px}

/* header */
.site-header{top:0;height:110px;background:var(--white)}
.brand{position:absolute;left:82px;top:22px;display:flex;align-items:center;gap:12px}
.brand-mark{width:52px;height:52px;border-radius:50%;background:var(--orange)}
.brand-name{font-size:22px;font-weight:700;color:var(--ink);line-height:1;width:110px}
.brand-tag{position:absolute;left:64px;top:60px;font-size:9px;color:var(--orange);font-weight:600;white-space:nowrap}
.main-nav{position:absolute;left:400px;top:44px;display:flex;gap:16px;font-size:14px;color:var(--ink)}
.main-nav .active{color:var(--orange)}
.site-header .btn{position:absolute;left:986px;top:32px;padding:10px 30px}

/* hero */
.hero{top:110px;height:600px;overflow:hidden}
.hero-photo{position:absolute;inset:0;background:linear-gradient(120deg,#8d8a86 0%,#c9c3ba 40%,#a39a8f 70%,#4e4e52 100%)}
.hero-shade{position:absolute;inset:0;background:rgba(30,30,30,.25)}
.hero-slant{position:absolute;left:0;bottom:0;width:1200px;height:110px}
.hero-copy{position:absolute;left:0;top:180px;width:1200px;text-align:center;color:var(--white)}
.hero-title{font-size:46px;font-weight:300;line-height:1.15;color:#f4e8d2}
.hero-title strong{font-weight:400;color:var(--white)}
.hero-lead{font-size:16px;width:900px;margin:22px auto 24px;line-height:1.5}

/* intro columns */
.intro{top:710px;height:480px}
.intro-col{position:absolute;top:60px;width:340px;text-align:center}
.intro-col + .intro-col{border-left:1px solid var(--line)}
.intro-col h2{font-size:26px;font-weight:400;color:var(--ink);line-height:1.05;margin-top:12px}
.intro-col h2 strong{font-weight:700;display:block}
.intro-col p{font-size:12.5px;line-height:1.9;margin:28px 26px 24px;color:var(--text)}
.intro-col .btn{padding:9px 30px;font-size:12.5px}
.intro-icon{height:48px;display:flex;justify-content:center;align-items:flex-end}

/* services */
.services{top:1190px;height:560px;overflow:hidden}
.services-bg{position:absolute;inset:0;background:linear-gradient(120deg,#ff7a2a 0%,#f26522 45%,#ff8f4a 70%,#e85a1c 100%)}
.section-title{text-align:center;font-size:30px;font-weight:400;color:var(--ink);line-height:1.15}
.section-title strong{display:block;font-weight:700}
.section-title::after{content:"";display:block;width:46px;height:3px;background:var(--orange);margin:10px auto 0}
.services .section-title{position:absolute;top:50px;width:1200px;color:var(--white)}
.services .section-title strong{color:var(--white)}
.services .section-title::after{background:var(--white)}
.usp-list{position:absolute;top:190px;left:75px;display:flex;gap:0}
.usp{width:150px;text-align:center;color:var(--white);font-size:13px;line-height:1.5}
.usp-badge{width:124px;height:124px;border-radius:50%;background:var(--ring);margin:0 auto;display:flex;align-items:center;justify-content:center}
.usp-core{width:92px;height:92px;border-radius:50%;background:#2c2c2e;display:flex;align-items:center;justify-content:center}
.usp-stem{width:2px;height:26px;background:rgba(255,255,255,.7);margin:0 auto}
.usp-dot{width:12px;height:12px;border-radius:50%;background:#2c2c2e;margin:0 auto 14px}
.usp strong{font-weight:700;display:block}
.usp small{font-size:11px;display:block}

/* process */
.process{top:1750px;height:575px}
.process .section-title{position:absolute;top:60px;width:1200px}
.steps{position:absolute;top:230px;left:70px;display:flex}
.step{width:212px;text-align:center}
.step-art{width:120px;height:150px;margin:0 auto 18px;border-radius:8px;background:linear-gradient(180deg,#fbe3d4,#f4f4f4)}
.step h3{font-size:15px;font-weight:500;color:var(--orange);line-height:1.5;width:150px;margin:0 auto}
.step p{font-size:11.5px;line-height:1.6;color:var(--text);width:170px;margin:12px auto 0}

/* help banner */
.help{top:2325px;height:460px;background:#f7f7f5;overflow:hidden}
.help-photo{position:absolute;right:0;top:0;width:520px;height:460px;background:linear-gradient(90deg,#f5f3ef 0%,#d9ccbd 40%,#9b8c7d 70%,#c7c1b8 100%)}
.help-copy{position:absolute;left:80px;top:80px;width:640px}
.help-copy p{font-size:29px;font-weight:400;color:var(--orange);line-height:1.45}
.help-copy h2{font-size:30px;font-weight:700;color:var(--ink);line-height:1.4;margin:16px 0 26px}

/* testimonials */
.testimonials{top:2785px;height:400px}
.testimonials .section-title{position:absolute;top:56px;width:1200px}
.quote{position:absolute;top:250px;width:520px;display:flex;align-items:flex-start;gap:24px}
.avatar{width:118px;height:118px;border-radius:50%;border:5px solid var(--orange);background:linear-gradient(160deg,#e8d5c6,#b79b87);flex:none}
.quote blockquote{font-size:12.5px;line-height:1.7;color:var(--text);padding-top:12px;position:relative}
.quote blockquote::before,.quote blockquote::after{font-size:40px;color:var(--ink);font-weight:700;position:absolute;line-height:1}
.quote blockquote::before{content:"\201C";left:-22px;top:6px}
.quote blockquote::after{content:"\201D";right:-4px;top:22px}
.quote cite{display:block;color:var(--orange);font-style:normal;margin-top:12px;font-size:12.5px}

/* business */
.business{top:3185px;height:215px;background:var(--lavender)}
.business-head{position:absolute;left:80px;top:70px;width:160px;text-align:center;font-size:28px;color:var(--ink);line-height:1.1;border-right:1px solid #bbb;padding-right:34px}
.business-head strong{display:block;font-weight:700}
.business h2{position:absolute;left:312px;top:40px;font-size:30px;font-weight:400;color:var(--ink)}
.business ul{position:absolute;left:312px;top:100px;list-style:none;font-size:14px;font-weight:700;color:var(--orange);line-height:1.95}
.business li::before{content:"•";margin-right:8px}

/* footer */
.site-footer{top:3400px;height:397px;background:var(--footer);color:#ddd}
.footer-col{position:absolute;top:70px}
.footer-col h4{font-size:18px;font-weight:400;color:var(--orange);padding-bottom:10px;border-bottom:1px solid #3a3a3a;margin-bottom:16px}
.footer-col ul{list-style:none;font-size:13px;line-height:1.7}
.quick li::before{content:"»";margin-right:8px;color:#ddd}
.contact-line{display:flex;gap:12px;font-size:12.5px;line-height:1.55;margin-bottom:12px;align-items:flex-start}
.contact-line .hot{color:var(--orange);font-size:15px}
.news p{font-size:12.5px;line-height:1.5}
.news .field{width:200px;height:28px;background:var(--white);margin:14px 0 14px;font-size:10px;color:#999;padding:8px}
.news .btn{border-radius:0;padding:6px 12px;font-size:11px}
.social li{display:flex;align-items:center;gap:12px;margin-bottom:10px}
.social .sq{width:22px;height:22px;background:#3a7fc4;border-radius:3px}
.legal{position:absolute;left:0;bottom:0;width:1200px;height:27px;background:var(--orange);color:var(--white);font-size:11px;text-align:center;line-height:27px}
</style>
</head>
<body>

<header class="site-header">
  <div class="brand">
    <span class="brand-mark"></span>
    <span class="brand-name">Handset Haven</span>
    <span class="brand-tag">We will come to you!</span>
  </div>
  <nav class="main-nav">
    <a class="active">Home</a><a>Who We Are</a><a>What We Do</a><a>Our Process</a><a>Pricing</a><a>Testimonials</a><a>Our Clients</a>
  </nav>
  <a class="btn">Contact Us</a>
</header>

<section class="hero">
  <div class="hero-photo" role="img" aria-label="Photo of an engineer in gloves repairing a smartphone on a workbench with tools"></div>
  <div class="hero-shade"></div>
  <div class="hero-copy">
    <h1 class="hero-title">Best Mobile Repair Service<br><strong>At Any Time In Anywhere</strong></h1>
    <p class="hero-lead">We are starting a new service that offers mobile device repairs on location, be it at the home of our customers, their office, or any other place. Just give us the address and we will come to you for the repair job.</p>
    <a class="btn">Call Now</a>
  </div>
  <svg class="hero-slant" viewBox="0 0 1200 110" preserveAspectRatio="none"><polygon points="0,110 1200,0 1200,110" fill="#fff"/></svg>
</section>

<section class="intro">
  <div class="intro-col" style="left:62px">
    <div class="intro-icon"><svg width="50" height="44" viewBox="0 0 50 44"><circle cx="25" cy="10" r="7" fill="#e8401c"/><circle cx="10" cy="22" r="6" fill="#e8401c"/><circle cx="40" cy="22" r="6" fill="#e8401c"/><path d="M14 44a11 11 0 0 1 22 0z" fill="#e8401c"/></svg></div>
    <h2>Who<strong>We Are</strong></h2>
    <p>Our company is based in Rotterdam, the Netherlands. We provide different services for all kinds of electronic devices. The kind of services we provide are, among other things, installations of hardware and software and the repair of broken or malfunctioning devices.</p>
    <a class="btn">Read More</a>
  </div>
  <div class="intro-col" style="left:430px">
    <div class="intro-icon"><svg width="30" height="48" viewBox="0 0 30 48"><rect x="2" y="2" width="26" height="44" rx="4" fill="none" stroke="#e8401c" stroke-width="3"/><rect x="7" y="9" width="16" height="26" fill="#e8401c"/><circle cx="15" cy="40" r="2" fill="#e8401c"/></svg></div>
    <h2>What<strong>We Do</strong></h2>
    <p>We are starting a new service that offers mobile device repairs on location, be it at the home of our customers, their office, or any other place. Just give us the address and we will come to you for the repair job. We offer a fully functional mobile repair center in the form of specially customized vans.</p>
    <a class="btn">Read More</a>
  </div>
  <div class="intro-col" style="left:798px">
    <div class="intro-icon"><svg width="34" height="46" viewBox="0 0 34 46"><circle cx="12" cy="8" r="6" fill="none" stroke="#e8401c" stroke-width="2"/><path d="M9 8v20l-5-4-3 3 10 14h18l3-16-11-4V8z" fill="#2b2b2b"/></svg></div>
    <h2>Why<strong>Choose Us</strong></h2>
    <p>We have multiple skilled engineers who drive trough the country on a daily basis and can be on location within a working day. Repair is done immediately onsite while the customer waits. Your phone is being repaired directly in front of you, the next business-day, on a location you desire.</p>
    <a class="btn">Read More</a>
  </div>
</section>

<section class="services">
  <div class="services-bg" role="img" aria-label="Orange-toned photo of a hand holding a smartphone"></div>
  <h2 class="section-title">Our<strong>Services</strong></h2>
  <div class="usp-list">
    <div class="usp"><div class="usp-badge"><div class="usp-core"><svg width="40" height="40" viewBox="0 0 40 40"><circle cx="22" cy="7" r="4" fill="#fff"/><path d="M18 13l-6 10h6l-4 14h4l8-14-4-2 4-6z" fill="#fff"/></svg></div></div><div class="usp-stem"></div><div class="usp-dot"></div><strong>Professional service</strong> on location. Don't ship to us we will come to you!</div>
    <div class="usp"><div class="usp-badge"><div class="usp-core"><svg width="40" height="40" viewBox="0 0 40 40"><circle cx="20" cy="16" r="10" fill="none" stroke="#fff" stroke-width="3"/><text x="20" y="21" font-size="13" fill="#fff" text-anchor="middle" font-family="Raleway,sans-serif" font-weight="700">$</text><rect x="8" y="30" width="24" height="5" rx="2" fill="#fff"/></svg></div></div><div class="usp-stem"></div><div class="usp-dot"></div><strong>Clear pricing upfront.</strong> No hidden cost.</div>
    <div class="usp"><div class="usp-badge"><div class="usp-core"><svg width="40" height="40" viewBox="0 0 40 40"><circle cx="20" cy="20" r="15" fill="none" stroke="#fff" stroke-width="3"/><path d="M14 12l4 0 2 5-3 2a11 11 0 0 0 5 5l2-3 5 2v4c-9 1-17-7-15-15z" fill="#fff"/></svg></div></div><div class="usp-stem"></div><div class="usp-dot"></div><strong>Backed by a professional call center</strong> open 12 hours a day and open on a Saturday as well.</div>
    <div class="usp"><div class="usp-badge"><div class="usp-core"><svg width="40" height="40" viewBox="0 0 40 40"><rect x="7" y="10" width="26" height="22" rx="3" fill="none" stroke="#fff" stroke-width="3"/><rect x="7" y="10" width="26" height="6" fill="#fff"/><circle cx="14" cy="23" r="2" fill="#fff"/><circle cx="20" cy="23" r="2" fill="#fff"/><circle cx="26" cy="23" r="2" fill="#fff"/></svg></div></div><div class="usp-stem"></div><div class="usp-dot"></div><strong>Next business-day</strong> repair.</div>
    <div class="usp"><div class="usp-badge"><div class="usp-core"><svg width="40" height="40" viewBox="0 0 40 40"><path d="M9 31l14-14M17 31L31 17" stroke="#fff" stroke-width="4" stroke-linecap="round"/><path d="M9 9l22 22" stroke="#fff" stroke-width="4" stroke-linecap="round"/></svg></div></div><div class="usp-stem"></div><div class="usp-dot"></div><strong>Backed by a professional repair center</strong> with more then 12 years of experience.</div>
    <div class="usp"><div class="usp-badge"><div class="usp-core"><svg width="40" height="40" viewBox="0 0 40 40"><circle cx="13" cy="14" r="5" fill="#fff"/><circle cx="27" cy="14" r="5" fill="#fff"/><path d="M4 32a9 9 0 0 1 18 0zM18 32a9 9 0 0 1 18 0z" fill="#fff"/></svg></div></div><div class="usp-stem"></div><div class="usp-dot"></div><strong>Repair is done by</strong> certified engineers.</div>
    <div class="usp"><div class="usp-badge"><div class="usp-core"><svg width="40" height="40" viewBox="0 0 40 40"><circle cx="20" cy="16" r="10" fill="#fff"/><path d="M13 24l-3 12 6-3 4 4 4-4 6 3-3-12z" fill="#fff"/><circle cx="20" cy="16" r="5" fill="#2c2c2e"/></svg></div></div><div class="usp-stem"></div><div class="usp-dot"></div><strong>1 year warranty</strong> on the repair.</div>
  </div>
</section>

<section class="process">
  <h2 class="section-title">Our<strong>Process</strong></h2>
  <div class="steps">
    <div class="step"><div class="step-art" role="img" aria-label="Cartoon character holding a phone"></div><h3>Choose your device and repair job</h3><p>Suspendisse iaculis elit nec ornare pellentes. Donec lacinia lectus malesuada.</p></div>
    <div class="step"><div class="step-art" role="img" aria-label="Cartoon character placing an order on a phone"></div><h3>Place the order</h3><p>Suspendisse iaculis elit nec ornare pellentes. Donec lacinia lectus malesuada.</p></div>
    <div class="step"><div class="step-art" role="img" aria-label="Cartoon character waiting beside a clock"></div><h3>Get a callback within the hour</h3><p>Suspendisse iaculis elit nec ornare pellentes. Donec lacinia lectus malesuada.</p></div>
    <div class="step"><div class="step-art" role="img" aria-label="Cartoon character holding a date and location sign"></div><h3>Set date and location</h3><p>Suspendisse iaculis elit nec ornare pellentes. Donec lacinia lectus malesuada.</p></div>
    <div class="step"><div class="step-art" role="img" aria-label="Cartoon engineer arriving at the customer"></div><h3>We will come to you</h3><p>Suspendisse iaculis elit nec ornare pellentes. Donec lacinia lectus malesuada.</p></div>
  </div>
</section>

<section class="help">
  <div class="help-photo" role="img" aria-label="Photo of a smiling customer talking on the phone"></div>
  <div class="help-copy">
    <p>You are not sure what the problem is with their device, and for this reason you are not sure what repair request they should order.</p>
    <h2>Dont Worry, You can always contact us whatever the problem you have.</h2>
    <a class="btn">Contact Us</a>
  </div>
</section>

<section class="testimonials">
  <h2 class="section-title">Clients'<strong>Testimonials</strong></h2>
  <div class="quote" style="left:82px">
    <div class="avatar" role="img" aria-label="Portrait of a client"></div>
    <blockquote>Donec turpis turpis, dapibus sed turpis vel, condimentum ultricies sem leo magna condimentum nulla.<cite>- Mira Kessel</cite></blockquote>
  </div>
  <div class="quote" style="left:612px">
    <div class="avatar" role="img" aria-label="Portrait of a client"></div>
    <blockquote>Donec turpis turpis, dapibus sed turpis vel, condimentum ultricies sem leo magna condimentum nulla.<cite>- Toma Reyes</cite></blockquote>
  </div>
</section>

<section class="business">
  <div class="business-head">For<strong>Businees</strong></div>
  <h2>The services we provide for corporate clients are-</h2>
  <ul>
    <li>In nec orci at diam sollicitudin mollis.</li>
    <li>Nunc venenatis ligula id purus varius, quis dapibus erat auctor.</li>
    <li>Suspendisse in diam vitae ex commodo commodo.</li>
  </ul>
</section>

<footer class="site-footer">
  <div class="footer-col quick" style="left:80px;width:200px">
    <h4>Quick Links</h4>
    <ul><li>Home</li><li>Who We Are</li><li>What We Do</li><li>Our Process</li><li>Pricing</li><li>Testimonials</li><li>Our Clients</li><li>Contact Us</li></ul>
  </div>
  <div class="footer-col" style="left:302px;width:285px">
    <h4>Contact Information</h4>
    <div class="contact-line"><svg width="12" height="16" viewBox="0 0 12 16"><path d="M6 0a6 6 0 0 1 6 6c0 4-6 10-6 10S0 10 0 6a6 6 0 0 1 6-6z" fill="#ddd"/><circle cx="6" cy="6" r="2" fill="#1b1d20"/></svg><span>Lorem ipsum dolor sit amet<br>555 014 7730<br>PO Box 4410 Harbor Lane 2087</span></div>
    <div class="contact-line"><svg width="12" height="16" viewBox="0 0 12 16"><rect x="1" y="0" width="10" height="16" rx="2" fill="#ddd"/><rect x="3" y="2" width="6" height="10" fill="#1b1d20"/></svg><span class="hot">Freecall 555 010 2468</span></div>
    <div class="contact-line"><svg width="14" height="10" viewBox="0 0 14 10"><rect width="14" height="10" rx="1" fill="#ddd"/><path d="M0 0l7 6 7-6" fill="none" stroke="#1b1d20"/></svg><span>hello@handsethaven.example</span></div>
  </div>
  <div class="footer-col news" style="left:640px;width:240px">
    <h4>Newsletter Signup</h4>
    <p>Please enter your email address below to receive our FREE newsletter</p>
    <div class="field">Your Email ID</div>
    <a class="btn">Subscribe</a>
  </div>
  <div class="footer-col social" style="left:934px;width:186px">
    <h4>Follow Us</h4>
    <ul><li><span class="sq"></span>Friendlink</li><li><span class="sq"></span>Worknet</li><li><span class="sq"></span>Chirper</li><li><span class="sq"></span>Email</li></ul>
  </div>
  <div class="legal">Copyright 2015@handsethaven.example. All Rights Are Reserved.</div>
</footer>

</body>
</html>
```